Furniture & Lighting Wholesaler Needs a Product Catalogue/Look Book

Our company, Vostre Merchant Co, imports quality hand-made furniture, lighting and decor from South Africa. Our products are well-designed and are designed to be used in up-market hotels and homes. Our primary customers are small- to medium-size retail shops.
We require a +/- 14-16 page look book (concept as per attached image) that will be used both in hard-copy and online. We have all of the necessary high-res images, descriptions/text etc. We need you to propose several design concepts from which we can choose, and then execute the design.
Please visit our website www.vostremerchant.example to see the products and their descriptions, as well as to get a feel for our style. Thank you for looking at our project!
Target Market(s)
Boutique Furniture Stores; Interior Designers
Industry/Entity Type
It Company
Font styles to use
Other font styles liked:
- Bauer Bodini and Open Sans Condensed
Look and feel
Each slider illustrates characteristics of the customer's brand and the style your logo design should communicate.

```html
<!DOCTYPE html>
<html lang="en">
<head>
<meta charset="utf-8">
<title>Vostre Merchant Co — Look Book, pages 8–9</title>
<link rel="stylesheet" href="https://fonts.googleapis.com/css2?family=Open+Sans:wght@300;400;600;700&display=swap">
<style>
  :root {
    --bg: #d9d9d9;
    --paper: #ffffff;
    --gold: #a99a6c;
    --gold-dark: #8f8157;
    --ink: #3a3a3a;
    --charcoal: #4a4a4a;
    --pill: #ececec;
  }
  * { box-sizing: border-box; margin: 0; padding: 0; }
  html, body { width: 1200px; height: 800px; overflow: hidden; }
  body {
    background: var(--bg);
    font-family: "Open Sans", Arial, sans-serif;
    color: var(--ink);
    position: relative;
  }
  .spread {
    position: absolute;
    left: 30px; top: 185px;
    width: 1140px; height: 430px;
    display: flex;
    box-shadow: 0 10px 30px rgba(0,0,0,.18);
  }
  .page {
    position: relative;
    width: 570px; height: 430px;
    background: var(--paper);
    overflow: hidden;
  }
  .page--left { box-shadow: inset -14px 0 18px -14px rgba(0,0,0,.18); }
  .page--right { box-shadow: inset 14px 0 18px -14px rgba(0,0,0,.18); }

  .product {
    position: absolute;
    width: 160px;
  }
  .product__photo {
    width: 132px; height: 120px;
    border: 2px solid var(--gold);
    border-radius: 18px;
    box-shadow: 0 3px 8px rgba(0,0,0,.18);
    margin-bottom: 10px;
  }
  .photo--chandelier-table { background: radial-gradient(circle at 50% 25%, #d9cdb4 0 18%, #3a3733 45%, #24221f 100%); }
  .photo--chandeliers { background: radial-gradient(circle at 50% 40%, #e8dfc9 0 30%, #6d6a63 60%, #2f3640 100%); }
  .photo--trunk-pale { background: linear-gradient(160deg, #f3f1ec 0 15%, #a89c8a 45%, #6f655a 100%); }
  .photo--trunk-dark { background: linear-gradient(160deg, #ffffff 0 15%, #4a4a46 40%, #2a2a28 100%); }
  .photo--side-table { background: radial-gradient(circle at 50% 45%, #8f8a80 0 20%, #f2f2f2 55%, #ffffff 100%); }

  .product__name {
    font-weight: 300;
    font-size: 12px;
    letter-spacing: .02em;
    color: var(--gold);
    text-transform: uppercase;
    margin-bottom: 3px;
  }
  .product__lead {
    font-size: 6.5px;
    font-weight: 700;
    line-height: 1.3;
    color: var(--ink);
    margin-bottom: 8px;
  }
  .product__price {
    display: inline-block;
    background: var(--gold);
    color: #fff;
    font-size: 14px;
    font-weight: 400;
    padding: 3px 12px;
    margin: 0 0 8px 12px;
    clip-path: polygon(3% 0, 100% 6%, 97% 100%, 0 94%);
  }
  .product__features {
    list-style: none;
    font-size: 7px;
    line-height: 1.55;
    color: var(--ink);
    padding-left: 10px;
  }
  .product__features li { position: relative; }
  .product__features li::before {
    content: "";
    position: absolute; left: -8px; top: 4.5px;
    width: 2.5px; height: 2.5px; border-radius: 50%;
    background: var(--ink);
  }

  .tab {
    position: absolute;
    width: 24px;
    background: var(--gold);
  }
  .tab--left { left: 0; top: 285px; height: 145px; border-radius: 0 16px 0 0; }
  .tab--right { right: 0; top: 0; height: 175px; border-radius: 0 0 0 16px; }
  .folio {
    position: absolute;
    width: 24px; height: 24px;
    background: var(--charcoal);
    color: #e0d9c2;
    font-size: 8px;
    display: flex; align-items: center; justify-content: center;
  }
  .folio--left { left: 0; bottom: 0; border-radius: 0 12px 0 0; }
  .folio--right { right: 0; top: 175px; border-radius: 0 0 0 12px; }

  .site {
    position: absolute;
    bottom: 10px;
    display: flex; align-items: center; gap: 6px;
    background: var(--pill);
    border-radius: 10px;
    padding: 3px 10px;
    font-size: 6px;
    color: #777;
  }
  .site__mark { width: 9px; height: 9px; border: 1.5px solid var(--charcoal); }
  .site--left { right: 22px; }
  .site--right { left: 22px; }
</style>
</head>
<body>
<main class="spread">
  <section class="page page--left">
    <article class="product" style="left:45px; top:115px;">
      <div class="product__photo photo--chandelier-table" role="img" aria-label="Photo of a beaded chandelier hanging above a pale wooden dining table"></div>
      <h2 class="product__name">Product Name</h2>
      <p class="product__lead">Faccuipa ipiim excearum rae expligent lam qui occupa rchicie ndesequi latur</p>
      <span class="product__price">$59.99</span>
      <ul class="product__features">
        <li>Sint labor sinvelluptat ulles erspellacil</li>
        <li>Es maximus si num ad etus</li>
        <li>Acerersped moluptaquate</li>
        <li>Eella cus cuptatem voles</li>
        <li>Bos es doluptatem inverchicils</li>
        <li>Wuidi dollorestrum</li>
        <li>Cus de nones mos ma idit res magnam</li>
        <li>Aut que ex enist fugitio restrunt</li>
      </ul>
    </article>
    <article class="product" style="left:225px; top:70px;">
      <div class="product__photo photo--chandeliers" role="img" aria-label="Photo of a cluster of cream fringed pendant chandeliers"></div>
      <h2 class="product__name">Product Name</h2>
      <p class="product__lead">Faccuipa ipiim excearum rae expligent lam qui occupa rchicie ndesequi latur</p>
      <span class="product__price">$59.99</span>
      <ul class="product__features">
        <li>Sint labor sinvelluptat ulles erspellacil</li>
        <li>Es maximus si num ad etus</li>
        <li>Acerersped moluptaquate</li>
        <li>Eella cus cuptatem voles</li>
        <li>Bos es doluptatem inverchicils</li>
        <li>Wuidi dollorestrum</li>
        <li>Cus de nones mos ma idit res magnam</li>
        <li>Aut que ex enist fugitio restrunt</li>
      </ul>
    </article>
    <article class="product" style="left:395px; top:25px;">
      <div class="product__photo photo--chandelier-table" role="img" aria-label="Photo of a beaded chandelier above a wooden table in a dark room"></div>
      <h2 class="product__name">Product Name</h2>
      <p class="product__lead">Faccuipa ipiim excearum rae expligent lam qui occupa rchicie ndesequi latur</p>
      <span class="product__price">$59.99</span>
      <ul class="product__features">
        <li>Sint labor sinvelluptat ulles erspellacil</li>
        <li>Es maximus si num ad etus</li>
        <li>Acerersped moluptaquate</li>
        <li>Eella cus cuptatem voles</li>
        <li>Bos es doluptatem inverchicils</li>
        <li>Wuidi dollorestrum</li>
        <li>Cus de nones mos ma idit res magnam</li>
        <li>Aut que ex enist fugitio restrunt</li>
      </ul>
    </article>
    <div class="tab tab--left"></div>
    <div class="folio folio--left">8</div>
    <div class="site site--left"><span class="site__mark"></span>www.vostremerchant.example</div>
  </section>

  <section class="page page--right">
    <article class="product" style="left:50px; top:65px;">
      <div class="product__photo photo--trunk-pale" role="img" aria-label="Photo of a pale hide-covered storage trunk"></div>
      <h2 class="product__name">Product Name</h2>
      <p class="product__lead">Faccuipa ipiim excearum rae expligent lam qui occupa rchicie ndesequi latur</p>
      <span class="product__price">$59.99</span>
      <ul class="product__features">
        <li>Sint labor sinvelluptat ulles erspellacil</li>
        <li>Es maximus si num ad etus</li>
        <li>Acerersped moluptaquate</li>
        <li>Eella cus cuptatem voles</li>
        <li>Bos es doluptatem inverchicils</li>
        <li>Wuidi dollorestrum</li>
        <li>Cus de nones mos ma idit res magnam</li>
        <li>Aut que ex enist fugitio restrunt</li>
      </ul>
    </article>
    <article class="product" style="left:220px; top:42px;">
      <div class="product__photo photo--trunk-dark" role="img" aria-label="Photo of a dark leather trunk with bone-inlay trim"></div>
      <h2 class="product__name">Product Name</h2>
      <p class="product__lead">Faccuipa ipiim excearum rae expligent lam qui occupa rchicie ndesequi latur</p>
      <span class="product__price">$59.99</span>
      <ul class="product__features">
        <li>Sint labor sinvelluptat ulles erspellacil</li>
        <li>Es maximus si num ad etus</li>
        <li>Acerersped moluptaquate</li>
        <li>Eella cus cuptatem voles</li>
        <li>Bos es doluptatem inverchicils</li>
        <li>Wuidi dollorestrum</li>
        <li>Cus de nones mos ma idit res magnam</li>
        <li>Aut que ex enist fugitio restrunt</li>
      </ul>
    </article>
    <article class="product" style="left:385px; top:20px;">
      <div class="product__photo photo--side-table" role="img" aria-label="Photo of a round side table on three crossed dark legs"></div>
      <h2 class="product__name">Product Name</h2>
      <p class="product__lead">Faccuipa ipiim excearum rae expligent lam qui occupa rchicie ndesequi latur</p>
      <span class="product__price">$59.99</span>
      <ul class="product__features">
        <li>Sint labor sinvelluptat ulles erspellacil</li>
        <li>Es maximus si num ad etus</li>
        <li>Acerersped moluptaquate</li>
        <li>Eella cus cuptatem voles</li>
        <li>Bos es doluptatem inverchicils</li>
        <li>Wuidi dollorestrum</li>
        <li>Cus de nones mos ma idit res magnam</li>
        <li>Aut que ex enist fugitio restrunt</li>
      </ul>
    </article>
    <div class="tab tab--right"></div>
    <div class="folio folio--right">9</div>
    <div class="site site--right"><span class="site__mark"></span>www.vostremerchant.example</div>
  </section>
</main>
</body>
</html>
```